Request for Business Card Design

Hi. My name is Marlene, I am looking for a new business card design for my company, Quarrow Signal Instruments, LLC. I really like the design you did for Tarsel Venture and was hoping you could do something similar using our full logo and our mark. I am also open to any raised texture design using our mark. I have attached our full logo, which would need to be somewhere on the card, as well as the mark in both outline and full form, as well as our brand colors / guide. The card does not have to be white, as long as our logo and mark appear. I actually like darker colored business cards more, but am open to all options. If you are interested in working with me, please let me know. We would also take the business card design into letterhead design if you can do that.

```html
<!DOCTYPE html>
<html lang="en">
<head>
<meta charset="utf-8">
<title>Quarrow Signal Instruments – Business Cards</title>
<link href="https://fonts.googleapis.com/css2?family=Titillium+Web:wght@600;700&family=Open+Sans:wght@400;600&display=swap" rel="stylesheet">
<style>
  :root {
    --ink: #151515;
    --ink-soft: #1d1d1d;
    --brand-blue: #0f9ac4;
    --paper: #ffffff;
    --text-dark: #262a2e;
    --text-light: #f2f2f2;
    --stage: #2a2a2c;
    --pale-blue: #eef3f7;
  }
  * { box-sizing: border-box; margin: 0; padding: 0; }
  html, body { width: 1200px; height: 900px; overflow: hidden; }
  body {
    background: var(--stage);
    font-family: "Open Sans", Arial, sans-serif;
    position: relative;
  }
  .card {
    position: absolute;
    width: 525px;
    height: 300px;
    border-radius: 4px;
    overflow: hidden;
    box-shadow: 0 12px 30px rgba(0,0,0,.45);
  }
  /* Front */
  .card-front {
    left: 50px; top: 70px;
    background: var(--ink);
    border-bottom: 4px solid var(--brand-blue);
    color: var(--text-light);
  }
  .wordmark {
    position: absolute; left: 40px; top: 30px;
    font-family: "Titillium Web", Arial, sans-serif;
    font-weight: 700;
    line-height: 1;
  }
  .wordmark-name { font-size: 44px; letter-spacing: 3px; text-transform: uppercase; }
  .wordmark-sub { font-size: 11px; letter-spacing: 1.5px; text-transform: uppercase; margin-top: 4px; }
  .person {
    position: absolute; left: 40px; top: 112px;
    padding-left: 18px;
    border-left: 8px solid var(--brand-blue);
  }
  .person-name {
    font-family: "Titillium Web", Arial, sans-serif;
    font-weight: 700; font-size: 22px; color: var(--brand-blue);
    text-transform: uppercase; line-height: 1;
  }
  .person-role { font-size: 13px; margin-top: 4px; }
  .address { position: absolute; left: 40px; top: 172px; font-size: 12px; line-height: 1.45; }
  .contacts { position: absolute; left: 40px; top: 214px; list-style: none; font-size: 12px; line-height: 1.55; }
  .contacts li { display: flex; align-items: center; gap: 8px; }
  .contacts svg { width: 11px; height: 11px; fill: var(--brand-blue); }
  .front-accent {
    position: absolute; right: -70px; bottom: -90px;
    width: 300px; height: 300px; border-radius: 50%;
    border: 46px solid var(--brand-blue);
  }
  /* Back */
  .card-back {
    left: 625px; top: 70px;
    background: var(--ink);
  }
  .back-texture {
    position: absolute; inset: 0;
    background: radial-gradient(circle at 50% 50%, #262626 0%, var(--ink-soft) 60%, #0f0f0f 100%);
  }
  .back-name {
    position: absolute; inset: 0;
    display: flex; align-items: center; justify-content: center;
    font-family: "Titillium Web", Arial, sans-serif;
    font-weight: 700; font-size: 30px; letter-spacing: 3px;
    color: var(--brand-blue); text-transform: uppercase;
  }
  /* White logo card */
  .card-logo {
    left: 337px; top: 520px;
    background: var(--paper);
    color: var(--text-dark);
  }
  .logo-circle-faint {
    position: absolute; left: 250px; top: 20px;
    width: 260px; height: 260px; border-radius: 50%;
    border: 40px solid var(--pale-blue);
  }
  .logo-lockup {
    position: absolute; inset: 0;
    display: flex; align-items: center; justify-content: center; gap: 18px;
  }
  .logo-dot { width: 46px; height: 46px; border-radius: 50%; background: var(--brand-blue); }
  .logo-text { font-family: "Titillium Web", Arial, sans-serif; font-weight: 700; line-height: 1; }
  .logo-text .wordmark-name { font-size: 50px; }
  .logo-text .wordmark-sub { font-size: 12.5px; }
</style>
</head>
<body>

  <section class="card card-front">
    <div class="wordmark">
      <div class="wordmark-name">Quarrow</div>
      <div class="wordmark-sub">Signal Instruments</div>
    </div>
    <div class="person">
      <div class="person-name">Evan Holt</div>
      <div class="person-role">Managing Director</div>
    </div>
    <p class="address">Your address, City<br>State, Zip 1234</p>
    <ul class="contacts">
      <li><svg viewBox="0 0 24 24"><path d="M6.6 10.8a15 15 0 0 0 6.6 6.6l2.2-2.2a1 1 0 0 1 1-.25 11.4 11.4 0 0 0 3.6.57 1 1 0 0 1 1 1V20a1 1 0 0 1-1 1A17 17 0 0 1 3 4a1 1 0 0 1 1-1h3.5a1 1 0 0 1 1 1c0 1.25.2 2.45.57 3.57a1 1 0 0 1-.25 1z"/></svg>123 456 789</li>
      <li><svg viewBox="0 0 24 24"><path d="M2 5h20v14H2z M2 5l10 8 10-8" fill="none" stroke="#0f9ac4" stroke-width="2.5"/></svg>info@quarrowsignal.com</li>
      <li><svg viewBox="0 0 24 24"><circle cx="12" cy="12" r="10"/></svg>www.quarrowsignal.com</li>
    </ul>
    <div class="front-accent"></div>
  </section>

  <section class="card card-back">
    <div class="back-texture" role="img" aria-label="Raised dark-on-dark repeating brand texture"></div>
    <div class="back-name">Quarrow</div>
  </section>

  <section class="card card-logo">
    <div class="logo-circle-faint"></div>
    <div class="logo-lockup">
      <div class="logo-dot"></div>
      <div class="logo-text">
        <div class="wordmark-name">QUARROW</div>
        <div class="wordmark-sub">SIGNAL INSTRUMENTS</div>
      </div>
    </div>
  </section>

</body>
</html>
```